Tech business card design

We need an amazing business card design for our new business 'Pexla' a marketing tech startup based in Sydney, Australia. We provide an online marketplace for businesses to search and buy advertising media, connect with service providers and learn more about marketing. We wish to communicate 'cool tech', reliability and professionalism and design based around our logo.

Target Market(s)

Business Owners

Contact Information for Business Card

Name
Position
Email Address
Website
Phone Number

Font styles to use
Other font styles liked:
• Avenir & Avenir Next

Colors

Designer to choose colors to be used in the design.

```html
<!DOCTYPE html>
<html lang="en">
<head>
<meta charset="utf-8">
<title>Pexla Business Card</title>
<link rel="stylesheet" href="https://fonts.googleapis.com/css2?family=Oswald:wght@500&family=Work+Sans:wght@400;800&display=swap">
<style>
  :root {
    --backdrop-top: #2b2b2b;
    --backdrop-bottom: #0d0d0d;
    --card: #1e1e1e;
    --card-edge: #262626;
    --ink: #f4f4f4;
    --ink-soft: #d8d8d8;
    --wordmark: #9a9a9a;
  }
  * { margin: 0; padding: 0; box-sizing: border-box; }
  html, body { width: 1200px; height: 900px; overflow: hidden; }
  body {
    background: radial-gradient(ellipse at 50% 30%, var(--backdrop-top), var(--backdrop-bottom) 75%);
    font-family: "Work Sans", Arial, sans-serif;
    color: var(--ink);
    position: relative;
  }
  .card {
    position: absolute;
    left: 290px;
    width: 620px;
    height: 354px;
    background: linear-gradient(135deg, var(--card), var(--card-edge));
    box-shadow: 0 18px 40px rgba(0,0,0,0.6);
  }
  .card--front { top: 78px; }
  .card--back { top: 468px; }

  .wordmark {
    position: absolute;
    left: 0; right: 0; top: 130px;
    text-align: center;
    font-family: "Work Sans", Arial, sans-serif;
    font-weight: 800;
    font-size: 80px;
    letter-spacing: -2px;
    color: var(--wordmark);
    line-height: 1;
  }

  .identity {
    position: absolute;
    right: 340px;
    top: 130px;
    text-align: right;
  }
  .identity__name {
    font-family: "Oswald", "Arial Narrow", sans-serif;
    font-weight: 500;
    font-size: 30px;
    text-transform: uppercase;
    letter-spacing: 0.3px;
    line-height: 1.1;
  }
  .identity__role {
    font-size: 16px;
    letter-spacing: 1px;
    color: var(--ink-soft);
    margin-top: 2px;
  }
  .divider {
    position: absolute;
    left: 300px;
    top: 140px;
    width: 2px;
    height: 66px;
    background: var(--ink);
  }
  .contacts {
    position: absolute;
    left: 326px;
    top: 134px;
    list-style: none;
  }
  .contacts__item {
    display: flex;
    align-items: center;
    gap: 14px;
    font-size: 18px;
    letter-spacing: 1px;
    line-height: 26px;
  }
  .contacts__icon { width: 13px; height: 13px; flex: none; }
  .address {
    position: absolute;
    left: 0; right: 0;
    bottom: 40px;
    text-align: center;
    font-size: 19px;
    letter-spacing: 1.2px;
  }
</style>
</head>
<body>
  <section class="card card--front">
    <div class="wordmark">Pexla</div>
  </section>

  <section class="card card--back">
    <div class="identity">
      <div class="identity__name">Daniel Reeve</div>
      <div class="identity__role">Director</div>
    </div>
    <div class="divider"></div>
    <ul class="contacts">
      <li class="contacts__item">
        <svg class="contacts__icon" viewBox="0 0 16 16" aria-hidden="true"><path d="M4 1h3l1 4-2 1.5a9 9 0 0 0 3.5 3.5L11 8l4 1v3c0 1-1 2-2 2A12 12 0 0 1 2 3c0-1 1-2 2-2z" fill="var(--ink)"/></svg>
        <span>+61 2 5550 1847</span>
      </li>
      <li class="contacts__item">
        <svg class="contacts__icon" viewBox="0 0 16 16" aria-hidden="true"><rect x="1.5" y="3.5" width="13" height="9" fill="none" stroke="var(--ink)" stroke-width="1.5"/><path d="M1.5 3.5 8 9l6.5-5.5" fill="none" stroke="var(--ink)" stroke-width="1.5"/></svg>
        <span>info@pexla.com</span>
      </li>
      <li class="contacts__item">
        <svg class="contacts__icon" viewBox="0 0 16 16" aria-hidden="true"><g fill="none" stroke="var(--ink)" stroke-width="1.2"><circle cx="8" cy="8" r="6.5"/><ellipse cx="8" cy="8" rx="3" ry="6.5"/><path d="M1.5 8h13M2.5 4.8h11M2.5 11.2h11"/></g></svg>
        <span>www.pexla.com</span>
      </li>
    </ul>
    <div class="address">218 Harbour Lane Sydney, NSW 2000</div>
  </section>
</body>
</html>
```